Veluxa Bone & Motion Business Card

Need a business card using the logo provided. I want brand side of the card to be grey with the logo in the center of the card in white.

On the other side I leave to the designers

Target Market(s)

Personal Injury Attorneys

Industry/Entity Type

Medical

Contact Information for Business Card

Name, CEO. Cell Phone, (Marlowe, Address, Phone) (Homestead, Address, Phone) (Tallahassee, Address, Phone)

Colors

Designer to choose only greyscale colors for use in the design.

Requirements
Must have
• Logo by itself on one side

```html
<!DOCTYPE html>
<html lang="en">
<head>
<meta charset="utf-8">
<title>Veluxa Bone &amp; Motion Business Card</title>
<link rel="stylesheet" href="https://fonts.googleapis.com/css2?family=Lato:wght@700&family=Montserrat:wght@500&family=Nunito:wght@400&display=swap">
<style>
  :root {
    --backdrop: #1a1a1a;
    --card-light: #b2b2b4;
    --card-dark: #98989c;
    --white: #ffffff;
    --ink: #1f1f1f;
    --icon-grey: #8e8e92;
  }
  html, body {
    margin: 0;
    width: 1200px;
    height: 1200px;
    overflow: hidden;
    background: var(--backdrop);
  }
  .card {
    position: absolute;
    left: 260px;
    width: 684px;
    height: 444px;
    background: linear-gradient(200deg, var(--card-light) 0%, var(--card-dark) 100%);
    box-shadow: 0 6px 18px rgba(0,0,0,0.55);
  }
  .card--front { top: 101px; }
  .card--back { top: 626px; }

  .wordmark {
    position: absolute;
    transform: translate(-50%, -50%);
    text-align: center;
    color: var(--white);
    font-family: "Lato", sans-serif;
    font-weight: 700;
    white-space: nowrap;
  }
  .card--front .wordmark { left: 342px; top: 222px; }
  .card--front .wordmark__name { font-size: 78px; letter-spacing: 12px; line-height: 1; margin-right: -12px; }
  .card--front .wordmark__tagline { font-size: 34px; letter-spacing: 7px; line-height: 1; margin-top: 14px; margin-right: -7px; }

  .card--back .wordmark { left: 164px; top: 222px; }
  .card--back .wordmark__name { font-size: 46px; letter-spacing: 7px; line-height: 1; margin-right: -7px; }
  .card--back .wordmark__tagline { font-size: 20px; letter-spacing: 4px; line-height: 1; margin-top: 9px; margin-right: -4px; }

  .divider {
    position: absolute;
    left: 340px;
    top: 154px;
    width: 1.5px;
    height: 140px;
    background: linear-gradient(to bottom, transparent, var(--white) 20%, var(--white) 80%, transparent);
  }
  .person {
    position: absolute;
    left: 394px;
    top: 80px;
  }
  .person__name {
    font-family: "Montserrat", sans-serif;
    font-weight: 500;
    font-size: 32px;
    letter-spacing: 4px;
    color: var(--white);
    line-height: 1;
  }
  .person__role {
    font-family: "Nunito", sans-serif;
    font-size: 19px;
    color: var(--ink);
    margin-top: 2px;
    line-height: 1;
  }
  .contact-item {
    position: absolute;
    left: 393px;
    height: 32px;
    display: flex;
    align-items: center;
  }
  .contact-item__icon {
    width: 32px;
    height: 32px;
    border-radius: 50%;
    background: var(--white);
    display: flex;
    align-items: center;
    justify-content: center;
    flex: none;
  }
  .contact-item__text {
    position: absolute;
    left: 62px;
    font-family: "Nunito", sans-serif;
    font-size: 15.5px;
    letter-spacing: 0.3px;
    line-height: 17px;
    color: var(--white);
    white-space: nowrap;
  }
  .rule {
    position: absolute;
    left: 455px;
    width: 35px;
    height: 1.5px;
    background: var(--ink);
  }
</style>
</head>
<body>

<section class="card card--front" aria-label="Brand side">
  <div class="wordmark">
    <div class="wordmark__name">VELUXA</div>
    <div class="wordmark__tagline">BONE &amp; MOTION</div>
  </div>
</section>

<section class="card card--back" aria-label="Contact side">
  <div class="wordmark">
    <div class="wordmark__name">VELUXA</div>
    <div class="wordmark__tagline">BONE &amp; MOTION</div>
  </div>

  <div class="divider"></div>

  <div class="person">
    <div class="person__name">MARLOWE</div>
    <div class="person__role">CEO</div>
  </div>

  <div class="contact-item" style="top:184px">
    <span class="contact-item__icon">
      <svg width="18" height="18" viewBox="0 0 18 18" fill="none" stroke="var(--icon-grey)" stroke-width="1.8" stroke-linejoin="round">
        <path d="M2 9 L9 2.5 L16 9"/><path d="M4 8 V15.5 H14 V8"/><path d="M7.5 15.5 V11 H10.5 V15.5"/>
      </svg>
    </span>
    <span class="contact-item__text">Street Address Here<br>Singapore, 2222</span>
  </div>
  <div class="rule" style="top:222px"></div>

  <div class="contact-item" style="top:234px">
    <span class="contact-item__icon">
      <svg width="18" height="14" viewBox="0 0 18 14" fill="none" stroke="var(--icon-grey)" stroke-width="1.5">
        <rect x="1" y="1" width="16" height="12"/><path d="M1 1 L9 8 L17 1"/>
      </svg>
    </span>
    <span class="contact-item__text">urname@email.com</span>
  </div>
  <div class="rule" style="top:268px"></div>

  <div class="contact-item" style="top:280px">
    <span class="contact-item__icon">
      <svg width="18" height="16" viewBox="0 0 18 16" fill="none" stroke="var(--icon-grey)" stroke-width="1.6" stroke-linejoin="round">
        <path d="M1.5 5 Q9 -0.5 16.5 5 L14.5 7 L12 5.5 L12 4 Q9 3 6 4 L6 5.5 L3.5 7 Z"/>
        <rect x="3.5" y="8" width="11" height="7" rx="1"/><circle cx="9" cy="11.5" r="1.6"/>
      </svg>
    </span>
    <span class="contact-item__text">+18 5521 3084 6617<br>+18 7340 2168 9925</span>
  </div>
  <div class="rule" style="top:323px"></div>

  <div class="contact-item" style="top:333px">
    <span class="contact-item__icon">
      <svg width="20" height="20" viewBox="0 0 20 20" fill="none" stroke="var(--icon-grey)" stroke-width="1.4">
        <circle cx="10" cy="10" r="8.5"/><ellipse cx="10" cy="10" rx="3.8" ry="8.5"/><path d="M1.5 10 H18.5 M3 5.5 H17 M3 14.5 H17"/>
      </svg>
    </span>
    <span class="contact-item__text">www.websitename.com</span>
  </div>
</section>

</body>
</html>
```